New Business Card for our Indoor Golf Training Facility

We are looking for designs for a new business card for our indoor golf training facility. Attached is our logo, our logo with our slogan, and here is our elevator pitch (What makes us different from the others) not sure if all the info will fit on one card, maybe you can condense the elevator pitch? here is the info

Elevator Pitch
We work with serious golfers and those that want to be serious golfers…
to make you better, faster, at all phases of the game…
We use the same state-of-the-art technology as professional golfers…
which produces data sets that shows your improvement in real time.
Our facility is available 24/7 to our members, which allows you to improve on your time.

our website: www.birchpinlinks.com

Target Market(s)

Golfers

Font styles to use
Serif
Sans Serif

Colors
ec1f27
f59195
fbd4d5
919191
d3d3d3
1b1b1b

Requirements
Must have
• our logo or our logo with the slogan, elevator pitch (can be condensed or shortened)

```html
<!DOCTYPE html>
<html lang="en">
<head>
<meta charset="utf-8">
<title>Birch Pin Links – Business Card</title>
<link href="https://fonts.googleapis.com/css2?family=Roboto:wght@400;500;700;900&family=Open+Sans:ital,wght@1,400;1,600&display=swap" rel="stylesheet">
<style>
  :root{
    --red:#ec1f27;
    --red-soft:#f59195;
    --red-pale:#fbd4d5;
    --grey:#919191;
    --grey-light:#d3d3d3;
    --ink:#1b1b1b;
    --paper:#ffffff;
    --backdrop:#e9e7e4;
  }
  *{box-sizing:border-box;margin:0;padding:0}
  html,body{width:1200px;height:911px;overflow:hidden}
  body{background:var(--backdrop);font-family:"Roboto",Arial,sans-serif;position:relative}

  .card{
    position:absolute;width:560px;height:320px;background:var(--paper);
    border-radius:22px;overflow:hidden;
    box-shadow:0 3px 0 var(--grey-light),0 10px 24px rgba(0,0,0,.12);
  }
  .card--front{left:70px;top:110px}
  .card--back{left:570px;top:480px}

  /* front */
  .contact{position:absolute;left:300px;top:24px;color:var(--grey);font-size:12px;line-height:1.45}
  .contact__name{color:var(--red);font-weight:700;font-size:22px;line-height:1.1}
  .contact__title{color:var(--ink);font-weight:500;font-size:12px;margin-bottom:6px}
  .contact__address{margin-bottom:6px}
  .contact__row{display:flex;align-items:center;gap:7px}
  .contact__row svg{width:11px;height:11px;flex:none}

  .band{position:absolute;left:0;right:0;top:192px;height:80px;display:flex}
  .band__dark{width:40%;background:var(--ink)}
  .band__red{flex:1;background:var(--red);display:flex;align-items:center;justify-content:flex-end;padding-right:30px}
  .band__name{color:var(--paper);font-weight:700;font-size:17px;letter-spacing:.06em;text-transform:uppercase}

  /* back */
  .brand{position:absolute;left:40px;top:36px}
  .brand__name{color:var(--red);font-weight:900;font-size:34px;line-height:1}
  .brand__slogan{margin-top:6px;color:var(--red-soft);font-size:13px}

  .pitch{position:absolute;left:30px;right:30px;top:118px;text-align:center}
  .pitch__head{color:var(--red);font-weight:900;font-size:17px;letter-spacing:.02em;margin-bottom:8px}
  .pitch__body{font-family:"Open Sans",Arial,sans-serif;font-style:italic;color:#555;font-size:11.5px;line-height:1.55}
  .social{margin-top:12px;color:var(--red);font-weight:500;font-size:12px}
</style>
</head>
<body>

  <section class="card card--front">
    <div class="contact">
      <p class="contact__name">Dana Whitfield</p>
      <p class="contact__title">CEO/Founder</p>
      <p class="contact__address">1840 W. Alder Rd, Unit B4<br>Maplecrest, OH 45099</p>
      <p class="contact__row">
        <svg viewBox="0 0 12 12"><path fill="var(--red)" d="M2.5 1l2 2.2-1 1.3c.7 1.5 1.7 2.5 3.1 3.1l1.3-1 2.1 2-1.2 1.6C5.3 10 2 6.7 1 2.3z"/></svg>
        513-555-0182
      </p>
      <p class="contact__row">
        <svg viewBox="0 0 12 12"><rect x="1" y="2.5" width="10" height="7" rx="1" fill="var(--red)"/><path d="M1.5 3l4.5 3.5L10.5 3" stroke="#fff" fill="none"/></svg>
        info@birchpinlinks.com
      </p>
      <p class="contact__row">
        <svg viewBox="0 0 12 12"><circle cx="6" cy="6" r="5" fill="var(--red)"/><path d="M1.5 6h9M6 1.5c-2 2.5-2 6.5 0 9M6 1.5c2 2.5 2 6.5 0 9" stroke="#fff" stroke-width=".8" fill="none"/></svg>
        www.birchpinlinks.com
      </p>
    </div>

    <div class="band">
      <div class="band__dark"></div>
      <div class="band__red"><span class="band__name">Birch Pin Links</span></div>
    </div>
  </section>

  <section class="card card--back">
    <div class="brand">
      <p class="brand__name">Birch Pin Links</p>
      <p class="brand__slogan">Par Is Good. Birdie Is Better. Be Better.</p>
    </div>

    <div class="pitch">
      <p class="pitch__head">ELEVATOR PITCH:</p>
      <p class="pitch__body">
        We work with serious golfers and those that want to be serious golfers…<br>
        to make you better, faster, at all phases of the game…<br>
        We use the same state-of-the-art technology as professional golfers…<br>
        which produces data sets that shows your improvement in real time.<br>
        Our facility is available 24/7 to our members, which allows you to improve on your time.
      </p>
      <p class="social">@birchpinlinks</p>
    </div>
  </section>

</body>
</html>
```